Need App for Impact Related Events

My app is to help with internal events. When you enter the prompted event code the next screen shows you everyone currently at the event. It will give you the ability to Start a conversation with someone you met at that event, or signal it is your turn to send a message. The next screen is a message thread with that person. I am looking for a design that incorporates the colors and ‘feel good’ emotion of our logo. I have pieced together a pretty good interpretation of what I’m looking for in the attached mockup by slicing and dicing designs. I also attached our logo mascot.Screens (see attached mockups)

Note 1: I do not like the picture on the screen used in screen one because it makes it seem like a dating app. I attached an alternative photo that can be used or present different ideas.

Note 2: On the login/signup screen (screen 2) I need an additional first and last name for login, you can try to fit this on one login screen or present a two step signup screen where that is presented in the second screen.

READ MOCKUP GUIDELINES UNDER Must Haves

Target Market(s)

People attending internal social impact events

Industry/Entity Type

Charity

Font styles to use
Sans Serif

Colors
86cfc6

Requirements
Must have
• Follow the screen mockups attached to project
• PLEASE READ
• I have provided a relatively close design of what I’m looking for in the mockups. Some screens need to be followed more closely to my design mockup than other. I have listed a guide below how how closely you should follow my mockup design exactly. Overall I would like to see some ideas of incorporating a few accent colors so it doesn’t appear SO Blue. I also attached some app inspiration designs I found from around the web
• Screen Mockup Guideline Follow %
• Screen 1: 65% - mostly on target, would like to see ways to make it not SO Blue and possibly creative places to add some explainer text describing the app
• Screen 2: 50% - general design idea is here, but more open
• Screen 3: 35% - a lot more room for design influence
• Screen 4: 70% - mostly on target, a little room for design influence/color scheme ideas
• Screen 5-6: 25% - a lot of room for design change/ideas/influence
• Screen 7-8: 80% - already very close to what I need, maybe open to slight sizing and color scheme ideas
• Screen 9: 15% - the most open for influence, only the general functionality of the screen is communicated here
Nice to have
• Please Read Mockup Guideline above. In large part I am looking for something to use some nice accent colors so it is not overwhelmingly blue and bring the whole design into a seamless style.
Should not have

```html
<!DOCTYPE html>
<html lang="en">
<head>
<meta charset="utf-8">
<title>Events</title>
<link rel="stylesheet" href="https://fonts.googleapis.com/css2?family=Montserrat:wght@400;500;600;700;800&display=swap">
<style>
  :root {
    --ink: #2b2b33;
    --muted: #6e6e78;
    --placeholder: #8a8a92;
    --line: #e6e6ea;
    --purple: #9b59d6;
    --purple-deep: #8a47cf;
    --pink: #d86fb4;
    --pink-soft: #d68fbe;
    --rose: #ee3f86;
    --rose-light: #f6a7c3;
    --teal: #86cfc6;
    --bg: #ffffff;
  }
  * { box-sizing: border-box; margin: 0; padding: 0; }
  html, body { width: 675px; height: 1200px; overflow: hidden; background: var(--bg); }
  body { font-family: "Montserrat", Arial, sans-serif; color: var(--ink); position: relative; }

  .page-title {
    position: absolute; left: 30px; top: 36px;
    font-size: 50px; font-weight: 800; letter-spacing: -0.5px;
  }
  .profile-avatar {
    position: absolute; left: 585px; top: 36px; width: 56px; height: 56px;
    border-radius: 50%; background: linear-gradient(135deg, #8d8d8d, #3f3f3f);
  }

  .search-bar {
    position: absolute; left: 58px; top: 140px; width: 563px; height: 72px;
    border: 2px solid var(--line); border-radius: 8px;
    display: flex; align-items: center; justify-content: space-between;
    padding: 0 26px 0 28px;
  }
  .search-placeholder { font-size: 26px; color: var(--placeholder); font-weight: 500; }

  .tabs { position: absolute; left: 196px; top: 243px; height: 68px; display: flex; align-items: center; }
  .tab { font-size: 27px; font-weight: 700; letter-spacing: 1.5px; }
  .tab-active {
    height: 68px; width: 164px; border-radius: 4px;
    background: linear-gradient(90deg, var(--purple), var(--pink-soft));
    color: #fff; display: flex; align-items: center; justify-content: center;
  }
  .tab-idle { margin-left: 34px; color: var(--ink); }

  .event-card {
    position: absolute; left: 29px; top: 338px; width: 617px; height: 468px;
    border-radius: 10px; overflow: hidden; background: #fff;
    box-shadow: 0 3px 12px rgba(0,0,0,0.16);
  }
  .event-cover {
    height: 300px;
    background:
      radial-gradient(circle at 30% 35%, var(--rose-light) 0 12%, transparent 30%),
      radial-gradient(circle at 70% 30%, var(--rose) 0 14%, transparent 32%),
      linear-gradient(135deg, #f48fb1, var(--rose) 55%, #f7c6d6);
  }
  .event-name { position: absolute; left: 18px; top: 322px; font-size: 38px; font-weight: 700; }
  .event-date { position: absolute; left: 18px; top: 380px; font-size: 26px; color: var(--muted); font-weight: 500; letter-spacing: 0.5px; }
  .attendees { position: absolute; right: 20px; top: 378px; display: flex; }
  .attendee {
    width: 66px; height: 66px; border-radius: 50%; border: 3px solid #fff;
    margin-left: 10px;
  }
  .attendee-1 { background: linear-gradient(135deg, #6b5a4f, #c7b4a4); }
  .attendee-2 { background: linear-gradient(135deg, #e7a48d, #7a4b3c); }
  .attendee-3 { background: linear-gradient(135deg, #4e3b34, #b98b74); }
  .attendee-more {
    background: var(--purple); color: #fff; font-size: 20px; font-weight: 700;
    display: flex; align-items: center; justify-content: center;
  }

  .action { position: absolute; top: 940px; width: 280px; text-align: center; }
  .action-create { left: 67px; }
  .action-code { left: 344px; }
  .action-icon {
    width: 86px; height: 86px; border-radius: 50%; margin: 0 auto;
    display: flex; align-items: center; justify-content: center;
  }
  .action-create .action-icon { background: var(--purple-deep); }
  .action-code .action-icon { background: var(--pink-soft); }
  .action-label {
    margin-top: 18px; font-size: 24px; font-weight: 600; letter-spacing: 1.5px;
    white-space: nowrap; line-height: 1;
  }

  .tab-bar { position: absolute; left: 0; top: 1080px; width: 675px; height: 120px; }
  .nav-icon { position: absolute; top: 46px; }
  .nav-dot { position: absolute; left: 61px; top: 20px; width: 12px; height: 12px; border-radius: 50%; background: var(--purple); }
  .fab {
    position: absolute; left: 285px; top: 2px; width: 104px; height: 104px; border-radius: 50%;
    background: linear-gradient(135deg, var(--purple), var(--pink));
    display: flex; align-items: center; justify-content: center;
  }
</style>
</head>
<body>
  <h1 class="page-title">Events</h1>
  <div class="profile-avatar" role="img" aria-label="Profile photo of the signed-in user"></div>

  <div class="search-bar">
    <span class="search-placeholder">Search for the events</span>
    <svg width="30" height="30" viewBox="0 0 30 30" aria-hidden="true">
      <circle cx="13" cy="13" r="9" fill="none" stroke="var(--teal)" stroke-width="3"/>
      <line x1="20" y1="20" x2="27" y2="27" stroke="var(--teal)" stroke-width="3" stroke-linecap="round"/>
    </svg>
  </div>

  <nav class="tabs">
    <span class="tab tab-active">INVITES</span>
    <span class="tab tab-idle">YOUR</span>
  </nav>

  <article class="event-card">
    <div class="event-cover" role="img" aria-label="Photo of pink party balloons"></div>
    <h2 class="event-name">Nadia's Party</h2>
    <p class="event-date">22 - Sep - 2018</p>
    <div class="attendees">
      <div class="attendee attendee-1" role="img" aria-label="Guest photo"></div>
      <div class="attendee attendee-2" role="img" aria-label="Guest photo"></div>
      <div class="attendee attendee-3" role="img" aria-label="Guest photo"></div>
      <div class="attendee attendee-more">9+</div>
    </div>
  </article>

  <div class="action action-create">
    <div class="action-icon">
      <svg width="34" height="34" viewBox="0 0 34 34" aria-hidden="true">
        <path d="M17 4v26M4 17h26" stroke="#fff" stroke-width="3.5" stroke-linecap="round"/>
      </svg>
    </div>
    <p class="action-label">CREATE EVENT</p>
  </div>

  <div class="action action-code">
    <div class="action-icon">
      <svg width="38" height="38" viewBox="0 0 38 38" aria-hidden="true" fill="none" stroke="#fff" stroke-width="3" stroke-linecap="round">
        <path d="M3 12V3h9M26 3h9v9M35 26v9h-9M12 35H3v-9"/>
        <line x1="10" y1="19" x2="28" y2="19"/>
      </svg>
    </div>
    <p class="action-label">ENTER CODE</p>
  </div>

  <footer class="tab-bar">
    <span class="nav-dot"></span>
    <svg class="nav-icon" style="left:42px" width="50" height="50" viewBox="0 0 50 50" aria-hidden="true" fill="none" stroke="var(--purple)" stroke-width="3.5" stroke-linejoin="round">
      <rect x="5" y="9" width="40" height="36" rx="3"/>
      <line x1="5" y1="19" x2="45" y2="19"/>
      <line x1="15" y1="4" x2="15" y2="12" stroke-linecap="round"/>
      <line x1="35" y1="4" x2="35" y2="12" stroke-linecap="round"/>
    </svg>
    <svg class="nav-icon" style="left:180px" width="46" height="46" viewBox="0 0 46 46" aria-hidden="true" fill="none" stroke="var(--purple)" stroke-width="3.5" stroke-linejoin="round">
      <path d="M23 5a18 17 0 1 1-9 32l-9 3 3-8A18 17 0 0 1 23 5z"/>
    </svg>
    <div class="fab">
      <svg width="36" height="36" viewBox="0 0 36 36" aria-hidden="true">
        <path d="M7 7l22 22M29 7L7 29" stroke="#fff" stroke-width="3.5" stroke-linecap="round"/>
      </svg>
    </div>
    <svg class="nav-icon" style="left:446px" width="46" height="48" viewBox="0 0 46 48" aria-hidden="true" fill="none" stroke="var(--purple)" stroke-width="3.5" stroke-linejoin="round">
      <path d="M23 5c-8 0-13 6-13 14v10l-5 7h36l-5-7V19c0-8-5-14-13-14z"/>
      <path d="M18 41a5 5 0 0 0 10 0"/>
    </svg>
    <svg class="nav-icon" style="left:580px" width="50" height="46" viewBox="0 0 50 46" aria-hidden="true" stroke="var(--purple)" stroke-width="3.5" stroke-linecap="round">
      <line x1="4" y1="14" x2="46" y2="14"/>
      <line x1="4" y1="32" x2="46" y2="32"/>
      <rect x="28" y="8" width="8" height="12" rx="2" fill="var(--purple)"/>
      <rect x="12" y="26" width="8" height="12" rx="2" fill="var(--purple)"/>
    </svg>
  </footer>
</body>
</html>
```